Web Design Project

I want customers to be able to book appointments to get their makeup done and make a deposit and also have a gallery where i put my portfolio images, i want it to be very simple yet elegant.

Target Market(s)

Women ranging from 18-40 that want to get their makeup done

Industry/Entity Type

Makeup

Font styles to use
Sans Serif
Decorative

Requirements
Nice to have
• easy scheduling option and option to pay service in full on website.

```html
<!DOCTYPE html>
<html lang="en">
<head>
<meta charset="utf-8">
<title>Mara Lune Makeup – Book Online</title>
<link rel="stylesheet" href="https://fonts.googleapis.com/css2?family=Arimo:wght@400;700&family=Julius+Sans+One&display=swap">
<style>
:root{
  --ink:#1b1b1b;
  --ink-soft:#232323;
  --bar:#2b2b2b;
  --white:#ffffff;
  --text:#222222;
  --muted:#666666;
  --accent:#b3141b;
  --accent-dark:#9a1016;
  --band:#e4e4e4;
  --side:#ebebeb;
  --side-head:#d9d9d9;
  --field-line:#a9a9a9;
  --foot-text:#d8d8d8;
}
*{margin:0;padding:0;box-sizing:border-box}
html,body{width:1200px;height:809px;overflow:hidden}
body{position:relative;background:var(--white);font-family:"Arimo",Arial,sans-serif;color:var(--text)}
.abs{position:absolute}

/* header */
.site-header{position:absolute;left:0;top:0;width:1200px;height:110px;background:var(--ink)}
.brand{position:absolute;left:238px;top:26px;font-family:"Julius Sans One",sans-serif;color:var(--white);font-size:31px;letter-spacing:2px;line-height:1}
.brand small{display:block;font-size:8px;letter-spacing:3px;margin-top:6px}
.nav{position:absolute;top:44px;left:500px;display:flex}
.nav-item{height:34px;border-left:1px solid #8a8a8a;padding:0 14px;text-align:center;color:var(--white)}
.nav-item:first-child{border-left:none}
.nav-item b{display:block;font-weight:400;font-size:11.5px;letter-spacing:.2px}
.nav-item span{display:block;font-size:9px;color:#cfcfcf;margin-top:9px}
.nav-item.active b{color:var(--accent)}

/* gallery strip */
.strip{position:absolute;left:0;top:110px;width:1200px;height:171px;background:#151515}
.strip .shot{position:absolute;top:0;width:120px;height:158px}

/* booking */
.page-title{position:absolute;left:238px;top:299px;font-family:"Julius Sans One",sans-serif;color:var(--accent);font-size:15px;letter-spacing:.5px}
.intro{position:absolute;left:238px;top:330px;width:490px;font-size:11px;line-height:16px}
.band{position:absolute;height:22px;background:repeating-linear-gradient(135deg,#e9e9e9 0 2px,#f6f6f6 2px 4px);font-size:11px;line-height:22px;padding-left:4px}
.field{position:absolute;height:16px;border:1px solid var(--field-line);background:var(--white);font-size:8.5px;line-height:14px;padding-left:4px}
.field .arrow{position:absolute;right:0;top:0;width:14px;height:14px;border-left:1px solid var(--field-line);background:#eee}
.field .arrow::after{content:"";position:absolute;left:3px;top:5px;border:4px solid transparent;border-top:4px solid #444}
.field.soft{border-color:#ccc;color:#888;font-style:italic}
.field.soft .arrow{border-color:#ccc;background:#ddd}
.note{position:absolute;font-size:8.5px;color:#777;font-style:italic}
.rule{position:absolute;left:238px;top:563px;width:487px;height:1px;background:#dcdcdc}
.btn{position:absolute;left:629px;top:578px;width:104px;height:21px;background:var(--accent-dark);color:var(--white);border-radius:2px;font-size:10px;line-height:21px;text-align:center}

.side{position:absolute;left:746px;top:328px;width:215px;height:270px;background:var(--side)}
.side-head{height:28px;background:var(--side-head);font-size:9.5px;font-weight:700;line-height:28px;padding-left:24px;position:relative}
.side-head svg{position:absolute;left:7px;top:8px}
.side-link{font-size:8.5px;color:#555;padding-left:15px;position:relative;height:23.5px}
.side-link::before{content:"?";position:absolute;left:4px;color:#bbb;font-weight:700}
.side p{font-size:8px;color:#666;line-height:11px;padding:0 4px}

/* footer */
.site-footer{position:absolute;left:0;top:639px;width:1200px;height:133px;background:var(--ink-soft);color:var(--foot-text)}
.hours{position:absolute;left:269px;top:20px;font-size:9.5px;line-height:16px;color:var(--white)}
.hours span{display:inline-block;width:40px}
.address{position:absolute;left:530px;top:18px;width:165px;font-size:9.5px;line-height:16px;color:var(--white)}
.phone{position:absolute;left:530px;top:74px;font-size:14px;color:var(--white)}
.card{position:absolute;top:88px;width:30px;height:19px;border-radius:2px;background:#e8e8e8}
.social{position:absolute;top:23px;width:22px;height:22px;background:var(--white)}
.store{position:absolute;top:64px;height:25px;background:#101010;border-radius:3px}
.legal{position:absolute;left:0;top:772px;width:1200px;height:37px;background:var(--bar);color:#aaa;font-size:9.5px;line-height:37px;text-align:center}
</style>
</head>
<body>

<header class="site-header">
  <div class="brand">MARA LUNE<small>MAKEUP BY</small></div>
  <nav class="nav">
    <div class="nav-item"><b>HOME</b><span>home page</span></div>
    <div class="nav-item" style="width:94px"><b>ABOUT US</b><span>Mara Lune</span></div>
    <div class="nav-item" style="width:94px"><b>PORTFOLIO</b><span>my work</span></div>
    <div class="nav-item" style="width:108px"><b>TESTIMONIALS</b><span>what client say</span></div>
    <div class="nav-item active" style="width:96px"><b>BOOK ONLINE</b><span>book appoiment</span></div>
  </nav>
</header>

<section class="strip">
  <div class="shot" style="left:0;background:linear-gradient(#2a211c,#8c6a58)" role="img" aria-label="Portfolio photo: makeup portrait"></div>
  <div class="shot" style="left:120px;background:linear-gradient(#d9d4d2,#b49a8e)" role="img" aria-label="Portfolio photo: makeup portrait"></div>
  <div class="shot" style="left:240px;background:linear-gradient(#5a4030,#a07a62)" role="img" aria-label="Portfolio photo: makeup portrait"></div>
  <div class="shot" style="left:360px;background:linear-gradient(#d6d2d2,#8a6a62)" role="img" aria-label="Portfolio photo: makeup portrait"></div>
  <div class="shot" style="left:480px;background:linear-gradient(#6e5648,#c49a80)" role="img" aria-label="Portfolio photo: makeup portrait"></div>
  <div class="shot" style="left:600px;background:linear-gradient(#4a3f3c,#a47e6e)" role="img" aria-label="Portfolio photo: makeup portrait"></div>
  <div class="shot" style="left:720px;background:linear-gradient(#111,#9c7a6a)" role="img" aria-label="Portfolio photo: makeup portrait"></div>
  <div class="shot" style="left:840px;background:linear-gradient(#d0d0d0,#3a3030)" role="img" aria-label="Portfolio photo: makeup portrait"></div>
  <div class="shot" style="left:960px;background:linear-gradient(#1a1414,#8a5a50)" role="img" aria-label="Portfolio photo: makeup portrait"></div>
  <div class="shot" style="left:1080px;background:linear-gradient(#cfc9c6,#8a6a5a)" role="img" aria-label="Portfolio photo: makeup portrait"></div>
</section>

<main>
  <h1 class="page-title">BOOK APPOINTMENT ONLINE</h1>
  <p class="intro">Lorem ipsum dolor sit amet, consectetuer adipiscing elit, sed diam nonummy nibh euismod tincidunt ut laoreet dolore magna aliquam erat volutpat.</p>

  <div class="band" style="left:238px;top:376px;width:495px">How many guests?</div>
  <div class="field" style="left:238px;top:402px;width:73px">Just me<span class="arrow"></span></div>
  <div class="note" style="left:314px;top:404px">(Returning customer? <span style="color:#333">Log in.</span>)</div>

  <div class="band" style="left:238px;top:441px;width:303px">What kind?</div>
  <div class="band" style="left:552px;top:441px;width:181px">With whom?</div>
  <div class="field soft" style="left:238px;top:467px;width:293px;height:19px;line-height:17px">Select a Service<span class="arrow" style="height:17px"></span></div>
  <div class="field soft" style="left:553px;top:467px;width:52px;font-style:normal">Anyone<span class="arrow"></span></div>

  <div class="band" style="left:238px;top:510px;width:495px">When?</div>
  <div class="field" style="left:238px;top:536px;width:111px;height:13px;line-height:11px">12/12/2014</div>
  <svg class="abs" style="left:353px;top:536px" width="15" height="13" viewBox="0 0 15 13" aria-hidden="true">
    <rect x="0" y="0" width="15" height="3" fill="#444"/>
    <g fill="#555"><rect x="1" y="4" width="2" height="2"/><rect x="4" y="4" width="2" height="2"/><rect x="7" y="4" width="2" height="2"/><rect x="10" y="4" width="2" height="2"/><rect x="1" y="7" width="2" height="2"/><rect x="4" y="7" width="2" height="2"/><rect x="7" y="7" width="2" height="2"/><rect x="10" y="7" width="2" height="2"/><rect x="1" y="10" width="2" height="2"/><rect x="4" y="10" width="2" height="2"/><rect x="7" y="10" width="2" height="2"/><rect x="10" y="10" width="2" height="2"/></g>
  </svg>
  <div class="field" style="left:382px;top:536px;width:142px">Anytime<span class="arrow"></span></div>
  <div class="rule"></div>
  <div class="btn">Find Appointments</div>

  <aside class="side">
    <div class="side-head"><svg width="10" height="12" viewBox="0 0 10 12" aria-hidden="true"><text x="1" y="11" font-size="13" font-weight="700" fill="#999" font-family="Arial, sans-serif">?</text></svg>How Do I...</div>
    <div style="height:12px"></div>
    <div class="side-link">View a previous booking?</div>
    <div class="side-link">Reserve multiple services?</div>
    <div class="side-link">View descriptions of services or packages?</div>
    <div class="side-head" style="margin-top:-5px"><svg width="12" height="13" viewBox="0 0 12 13" aria-hidden="true"><circle cx="6" cy="3.5" r="3" fill="#999"/><path d="M0 13c0-4 3-6 6-6s6 2 6 6z" fill="#999"/></svg>My Appointments</div>
    <div style="height:16px"></div>
    <p>View upcoming appointments or quickly re-book past appointments.</p>
    <p style="margin-top:11px">If you've already booked with us, <span style="color:#333">Log in »</span></p>
  </aside>
</main>

<footer class="site-footer">
  <svg class="abs" style="left:239px;top:20px" width="16" height="16" viewBox="0 0 16 16" aria-hidden="true"><circle cx="8" cy="8" r="7" fill="none" stroke="#777" stroke-width="1.6"/><path d="M8 4v4.5h3" fill="none" stroke="#777" stroke-width="1.6"/></svg>
  <div class="hours"><span>Mon - Fri</span>: 9:00am to 7:00pm<br><span>Sat</span>: 8:00am to 4:00pm<br><span>Sun</span>: Closed</div>
  <svg class="abs" style="left:240px;top:90px" width="16" height="11" viewBox="0 0 16 11" aria-hidden="true"><rect x="0" y="0" width="16" height="11" rx="1" fill="#777"/><rect x="0" y="3" width="16" height="2" fill="#333"/></svg>
  <div class="card" style="left:270px"></div>
  <div class="card" style="left:302px;background:#d9d9d9"></div>
  <div class="card" style="left:334px;background:#f0e4da"></div>

  <svg class="abs" style="left:503px;top:19px" width="12" height="17" viewBox="0 0 12 17" aria-hidden="true"><path d="M6 0a6 6 0 0 1 6 6c0 4-6 11-6 11S0 10 0 6a6 6 0 0 1 6-6z" fill="#777"/><circle cx="6" cy="6" r="2.2" fill="#232323"/></svg>
  <div class="address">Lorem ipsum dolor sit amet, consec-tetuer adipiscing elit, sed diam, nonummy nibh euismod tincidunt</div>
  <svg class="abs" style="left:501px;top:76px" width="17" height="13" viewBox="0 0 17 13" aria-hidden="true"><path d="M1 4c0-3 15-3 15 0v2h-4V4H5v2H1z" fill="#777"/><rect x="3" y="7" width="11" height="6" rx="1" fill="#777"/></svg>
  <div class="phone">0123 456 789</div>

  <div class="social" style="left:797px"></div>
  <div class="social" style="left:825px"></div>
  <div class="social" style="left:853px"></div>
  <div class="social" style="left:881px"></div>
  <div class="social" style="left:909px"></div>
  <div class="social" style="left:937px"></div>
  <div class="store" style="left:801px;width:74px"></div>
  <div class="store" style="left:880px;width:76px"></div>
</footer>

<div class="legal">Copyright © 2014 by Mara Lune. All rights reserved.</div>

</body>
</html>
```